Business Cards for new orthopaedic surgery practice

My husband and I are starting our own orthopaedic surgery practice. We are looking for a business card that is uniform, but one will have my name/title and the other will have his. You can just create one design with my name on it for now. But when I choose your design as the winning design I will ask that you add another copy with his name/title.

We are looking for classy, simple, elite all in one. We like dark blues/a little gold/yellow. Something that goes with our logo. We want our logo incorporated. Here is all the info you need:
Business name: RV Bone & Vitality Center
Location: 38517 North Willowmere Ave
Maple Hollow, FL 33990
Phone: 954-218-4063
Fax: 954-582-7341
Email: info@myrvbonecare.example

Names: Lydia Vance, M.D.
Board Certified Hand and Upper Extremity Surgeon

Ebo Dansu, M.D.
Board Certified Hip & Knee Replacement/General Orthopaedic Surgeon

Can decide what you want to put on the back. Maybe a slogan:
Grounded in Care. Centered on You

I am just going to upload our logo. The only thing is if we select you as the winning design, the location, and phone numbers may change. We will need your help to update that once fully solidified.

Industry/Entity Type

Medical

Contact Information for Business Card

Colors
0054AA
0677BA
7BADD7
CADEEF
E8F1F8
0094D4
00A9DD
6FCCEA
C7EBF8
E9F6FB

Requirements
Must have
• class, appeal,
Should not have
• We want to air on the side of masculine if we are looking at masculine vs. feminine feel. But we still want it classy, sophisticated, and something we will love

```html
<!DOCTYPE html>
<html lang="en">
<head>
<meta charset="utf-8">
<title>RV Bone &amp; Vitality Center — Business Card</title>
<link rel="stylesheet" href="https://fonts.googleapis.com/css2?family=Montserrat:wght@400;500;700&display=swap">
<style>
  :root {
    --backdrop: #4a4a4c;
    --navy: #1b2a52;
    --gold: #c9a25a;
    --white: #ffffff;
    --soft-white: #e9edf5;
  }
  * { box-sizing: border-box; margin: 0; padding: 0; }
  html, body {
    width: 1200px; height: 875px; overflow: hidden;
    background: var(--backdrop);
    font-family: "Montserrat", Arial, sans-serif;
  }
  .stage {
    width: 1200px; height: 875px;
    display: flex; flex-direction: column; align-items: center; justify-content: center;
    gap: 40px;
  }
  .card {
    position: relative;
    width: 660px; height: 377px;
    background: var(--navy);
    border-radius: 22px;
    box-shadow: 0 14px 30px rgba(0,0,0,0.35);
    color: var(--white);
  }
  /* Brand mark: invented name with one plain circle */
  .brand {
    position: absolute;
    display: flex; flex-direction: column; align-items: center; gap: 12px;
    text-align: center;
  }
  .brand-circle {
    border: 2px solid var(--gold);
    border-radius: 50%;
  }
  .brand-name {
    font-weight: 500;
    color: var(--white);
    letter-spacing: 0.12em;
    text-transform: uppercase;
    line-height: 1.35;
  }
  /* Front */
  .card-front .brand { left: 50%; top: 62px; transform: translateX(-50%); }
  .card-front .brand-circle { width: 90px; height: 90px; }
  .card-front .brand-name { font-size: 17px; white-space: nowrap; }
  .slogan {
    position: absolute; left: 0; right: 0; top: 262px;
    text-align: center; font-size: 17px; font-weight: 400;
    color: var(--soft-white); letter-spacing: 0.02em;
  }
  /* Back */
  .card-back .brand { right: 40px; top: 30px; }
  .card-back .brand-circle { width: 64px; height: 64px; }
  .card-back .brand-name { font-size: 11px; }
  .doctor { position: absolute; left: 44px; top: 180px; }
  .doctor-name {
    font-size: 22px; font-weight: 700; color: var(--gold);
    letter-spacing: 0.02em; text-transform: uppercase;
  }
  .doctor-title { font-size: 13.5px; font-weight: 400; margin-top: 4px; }
  .rule {
    position: absolute; left: 44px; right: 40px; top: 240px;
    height: 1px; background: var(--gold);
  }
  .address {
    position: absolute; right: 40px; top: 258px;
    text-align: right; font-size: 13.5px; line-height: 1.5;
  }
  .contact { position: absolute; left: 44px; top: 258px; list-style: none; }
  .contact li {
    display: flex; align-items: center; gap: 10px;
    font-size: 13.5px; line-height: 1.7;
  }
  .contact svg { width: 13px; height: 13px; fill: var(--gold); flex: none; }
</style>
</head>
<body>
<main class="stage">

  <section class="card card-front" aria-label="Business card front">
    <div class="brand">
      <span class="brand-circle"></span>
      <span class="brand-name">RV Bone &amp; Vitality Center</span>
    </div>
    <p class="slogan">Grounded in Care. Centered on You</p>
  </section>

  <section class="card card-back" aria-label="Business card back">
    <div class="brand">
      <span class="brand-circle"></span>
      <span class="brand-name">RV Bone &amp;<br>Vitality Center</span>
    </div>

    <div class="doctor">
      <h1 class="doctor-name">Lydia Vance, M.D.</h1>
      <p class="doctor-title">Board Certified Hand and Upper Extremity Surgeon</p>
    </div>

    <div class="rule"></div>

    <p class="address">38517 North Willowmere Ave<br>Maple Hollow, FL 33990</p>

    <ul class="contact">
      <li>
        <svg viewBox="0 0 24 24" aria-hidden="true"><path d="M6.6 10.8a15.1 15.1 0 0 0 6.6 6.6l2.2-2.2c.3-.3.7-.4 1-.2 1.1.4 2.3.6 3.6.6.6 0 1 .4 1 1V20c0 .6-.4 1-1 1A17 17 0 0 1 3 4c0-.6.4-1 1-1h3.5c.6 0 1 .4 1 1 0 1.3.2 2.5.6 3.6.1.3 0 .7-.2 1z"/></svg>
        954-218-4063
      </li>
      <li>
        <svg viewBox="0 0 24 24" aria-hidden="true"><path d="M6 2h12v6H6zM3 9h18a1 1 0 0 1 1 1v7h-4v5H6v-5H2v-7a1 1 0 0 1 1-1zm5 8v3h8v-3z"/></svg>
        954-582-7341
      </li>
      <li>
        <svg viewBox="0 0 24 24" aria-hidden="true"><path d="M2 5h20v14H2zm2 2v.5l8 5 8-5V7l-8 5z"/></svg>
        info@myrvbonecare.example
      </li>
    </ul>
  </section>

</main>
</body>
</html>
```